Preisliste für Kosmetikinstitut
Zielgruppe
Ich benötige für mein Kosmetikinstitut eine Preisliste für die moderne Frau, aber auch Männer. Das Design sollte mein Logo enthalten. Farben des Designkonzepts einbauen.
A4 quer zum Falten, wie ein Heft, 1. Seite Preisliste mit logo, im Innenteil dann Anwendungen
Aufgabenstellung
Minimalistisch, ästhetisch, modern, edel
Kontaktdaten auf der Rückseite
LB Hautatelier
Lotte Brenner
Lindenhang 17
83671 Waakirchen
EMail: lotte@lb-hautatelier.de
Whatsapp: 0176 284 9017

```html
<!DOCTYPE html>
<html lang="de">
<head>
<meta charset="utf-8">
<title>Preisliste – Apparative Behandlungen</title>
<link href="https://fonts.googleapis.com/css2?family=Alegreya+Sans:wght@400;500;700;800&display=swap" rel="stylesheet">
<style>
  :root{
    --ink:#5d6966;
    --panel:#eeedeb;
    --paper:#ffffff;
    --stone-light:#e6e6e6;
    --stone-mid:#cfcfcf;
    --stone-dark:#ababab;
  }
  *{margin:0;padding:0;box-sizing:border-box}
  html,body{width:1200px;height:848px;overflow:hidden;background:var(--paper)}
  .spread{position:relative;width:1200px;height:848px;background:var(--paper);color:var(--ink);
    font-family:"Alegreya Sans",sans-serif;font-size:16px;line-height:20px;
    font-variant-numeric:oldstyle-nums}
  .texture{position:absolute;left:497px;top:0;width:186px;height:317px;
    background:linear-gradient(135deg,var(--stone-dark) 0%,var(--stone-light) 30%,var(--stone-mid) 52%,var(--stone-light) 72%,#bdbdbd 100%)}
  .panel{position:absolute;left:632px;top:28px;width:550px;height:797px;background:var(--panel)}
  .block{position:absolute;white-space:nowrap}
  .section-title{font-weight:700;letter-spacing:1.7px;font-size:17.4px;line-height:20px;text-transform:uppercase}
  .item-title{font-weight:700;letter-spacing:1.5px;font-size:16px;line-height:20px;text-transform:uppercase}
  .price-row{display:flex;font-weight:700;letter-spacing:1.4px;font-size:15.2px;line-height:20px;text-transform:uppercase}
  .price-row .label{width:310px;flex:none}
  .price{display:inline-flex;letter-spacing:.6px}
  .price .amount{width:48px;text-align:right}
  .price.wide .amount{width:auto;text-align:left;margin-left:10px}
  .steps{list-style:none}
  .steps li{display:grid;grid-template-columns:26px auto}
  .copy p+p{margin-top:4px}
  .extras .price-row{font-size:16.2px;line-height:24.4px}
  u{text-underline-offset:2px}
</style>
</head>
<body>
<main class="spread">
  <div class="texture" role="img" aria-label="Foto einer hellgrauen, modellierten Gipsstruktur mit weichen Wellen"></div>
  <div class="panel"></div>

  <h1 class="block section-title" style="left:109px;top:65px;">Apparative Behandlungen</h1>

  <section class="block" style="left:109px;top:115px;">
    <div class="item-title">Hydrofresh –</div>
    <div class="price-row"><span class="label">„Glowing Skin“ Treatment</span><span class="price">€ 59,00</span></div>
  </section>

  <section class="block" style="left:109px;top:164px;">
    <p>In <u>6 Schritten</u> zu einer Haut mit einmaligem Glow- Effekt:</p>
    <ol class="steps" style="margin-top:3px">
      <li><span>1.</span><span>Behandlungsschritt: die Haut wird tiefengereinigt</span></li>
      <li><span>2.</span><span>Behandlungsschritt: die obersten Verhornungen und<br>Schuppen werden sanft mit einem Peeling gelöst</span></li>
      <li><span>3.</span><span>Behandlungsschritt: die Haut wird in der Tiefe gereinigt<br>und entschlackt</span></li>
      <li><span>4.</span><span>Behandlungsschritt: niedermolekulare Wirkstoffe werden<br>aufgebracht, um die Haut zu erfrischen und den ent-<br>sprechenden Glow zu geben</span></li>
      <li><span>5.</span><span>Ausgewählte und hochdosierte Wirkstoffessenzen werden auf die<br>Haut gesprüht und durch die niedrige Molekularstruktur können<br>diese tiefer in der Haut wirken</span></li>
      <li><span>6.</span><span>Zum Schluss werden die Essenzen durch eine Impulsgebende<br>Druckluftmassage noch tiefer in die Haut gebracht; 60min</span></li>
    </ol>
  </section>

  <section class="block" style="left:109px;top:476px;">
    <h2 class="item-title">Mikrodermabrasion</h2>
    <div style="margin-top:5px">
      <div class="price-row"><span class="label">Gesicht</span><span class="price"><span>€</span><span class="amount">89,00</span></span></div>
      <div class="price-row"><span class="label">Gesicht, Hals, Dekolleté</span><span class="price"><span>€</span><span class="amount">110,00</span></span></div>
    </div>
    <div class="copy" style="margin-top:9px">
      <p>Bei der Mikrodermabrasion handelt es sich um ein mechanisches<br>Hautpeeling, dabei werden mittels feinster Kristalle die Hornzellen<br>der obersten Hautschicht schonend abgetragen und dann mit Hilfe<br>eines Unterdrucks behutsam abgesaugt.</p>
      <p>Der revitalisierende Prozess erhöht die Durchblutung, fördert die<br>Zellerneuerung und verleiht ihrer Haut ein zartes frisches Gefühl.<br>Die Haut gewinnt an Spannkraft, feine Fältchen werden gemildert<br>und Poren sichtbar verkleinert.</p>
      <p>Außerdem hilft es bei oberflächlichen Akne Narben, Pigment-<br>störungen und Dehnungsstreifen. Wirkstoffe können nun wieder<br>besser von der Haut aufgenommen werden.</p>
    </div>
  </section>

  <section class="block" style="left:702px;top:65px;">
    <h2 class="item-title">Microneedling</h2>
    <div style="margin-top:5px">
      <div class="price-row"><span class="label">Gesicht</span><span class="price"><span>€</span><span class="amount">110,00</span></span></div>
      <div class="price-row"><span class="label">Gesicht, Hals</span><span class="price"><span>€</span><span class="amount">130,00</span></span></div>
      <div class="price-row"><span class="label">Gesicht, Hals, Dekolleté</span><span class="price"><span>€</span><span class="amount">150,00</span></span></div>
    </div>
    <div class="copy" style="margin-top:9px">
      <p>Die Behandlung eignet sich besonders für Menschen, die<br>ihre Hautqualität verbessern und Falten, (Akne)Narben,<br>Pigmentverschiebungen, große Poren und sogar Haarausfall<br>behandeln wollen.</p>
      <p>Mit Hilfe feinster Nadeln werden der Haut kontrolliert</p>
      <p>Mikroverletzungen zugeführt, dies regt die natürliche Wund-<br>heilung, sowie Kollagen- und Elastin Bildung an.</p>
      <p>Microneedling ist also eine natürliche Beauty-Behandlung, die<br>körpereigene Reparaturmechanismen nutzt, um ein strafferes<br>Hautbild zu erhalten. Bereits nach der ersten Behandlung sieht die<br>Haut aufgepolstert, frisch und rosig aus.</p>
      <p>Kleine Linien und Fältchen werden tiefenbehandelt. Die Haut wirkt<br>straffer und jugendlicher. Ein weiterer Vorteil, durch die Stichkanäle<br>können Wirkstoffe besser von der Haut aufgenommen werden.</p>
    </div>
  </section>

  <section class="block extras" style="left:702px;top:497px;">
    <h2 class="section-title" style="font-size:18px">Zusatzleistungen</h2>
    <div style="margin-top:19px">
      <div class="price-row"><span class="label">Augenbrauen zupfen</span><span class="price wide"><span>€</span><span class="amount">08,00</span></span></div>
      <div class="price-row"><span class="label">Augenbrauen färben</span><span class="price wide"><span>€</span><span class="amount">12,00</span></span></div>
      <div class="price-row"><span class="label">Wimpern färben</span><span class="price wide"><span>€</span><span class="amount">15,00</span></span></div>
      <div class="price-row"><span class="label">Enthaarung</span><span class="price wide"><span>€</span><span class="amount">10,00-30,00</span></span></div>
    </div>
    <p style="margin-top:-2px">Enthaarung der störenden<br>Gesichtsbehaarung mittels Wax.</p>
  </section>
</main>
</body>
</html>
```